Business Card Design

WE are looking for a premium quality Business Cards for a Law Firm . Copies of our current business card is attached.

Contact Information for Business Card

xyz

```html
<!DOCTYPE html>
<html lang="en">
<head>
<meta charset="utf-8">
<title>Harlow Legal – Business Card</title>
<link rel="stylesheet" href="https://fonts.googleapis.com/css2?family=Arimo:wght@400;700&display=swap">
<style>
  :root {
    --backdrop: #141414;
    --card: #2b2b2c;
    --card-edge: #c8953f;
    --gold: #d19c47;
    --ink: #f2f2f2;
    --ink-soft: #e0e0e0;
    --mark-faint: rgba(255,255,255,0.045);
  }
  * { box-sizing: border-box; margin: 0; padding: 0; }
  html, body {
    width: 1200px; height: 963px; overflow: hidden;
    background: var(--backdrop);
    font-family: "Arimo", Arial, sans-serif;
  }
  .stage {
    width: 1200px; height: 963px;
    display: flex; align-items: center; justify-content: center;
  }
  .card {
    position: relative;
    width: 900px; height: 514px;
    background: var(--card);
    border-radius: 34px;
    box-shadow: 0 6px 0 var(--card-edge), 0 24px 50px rgba(0,0,0,0.6);
    overflow: hidden;
    color: var(--ink);
  }
  .card__watermark {
    position: absolute; left: 500px; top: 190px;
    width: 400px; height: 400px; border-radius: 50%;
    border: 22px solid var(--mark-faint);
  }
  .brand {
    position: absolute; left: 270px; top: 40px;
    display: flex; align-items: center; gap: 28px;
  }
  .brand__circle {
    width: 118px; height: 118px; border-radius: 50%;
    border: 6px solid var(--gold);
  }
  .brand__name {
    font-weight: 700; font-size: 52px; letter-spacing: 1px;
    color: var(--ink); text-transform: uppercase;
  }
  .person {
    position: absolute; left: 52px; top: 178px;
    padding-left: 26px;
    border-left: 12px solid var(--gold);
  }
  .person__name {
    font-weight: 700; font-size: 30px; color: var(--gold);
    text-transform: uppercase; line-height: 1.1;
  }
  .person__role { font-size: 21px; margin-top: 6px; text-transform: uppercase; }
  .person__credentials { font-size: 20px; margin-top: 4px; color: var(--ink-soft); }
  .contacts {
    position: absolute; left: 60px; top: 318px;
    list-style: none;
  }
  .contacts__item {
    display: flex; align-items: center; gap: 16px;
    font-size: 21px; height: 40px;
  }
  .contacts__icon { width: 20px; height: 20px; flex: none; }
  .address {
    position: absolute; left: 560px; top: 388px;
    font-size: 22px; line-height: 1.4; font-style: normal;
  }
</style>
</head>
<body>
<main class="stage">
  <article class="card">
    <div class="card__watermark" aria-hidden="true"></div>

    <header class="brand">
      <div class="brand__circle" aria-hidden="true"></div>
      <h1 class="brand__name">Harlow Legal</h1>
    </header>

    <section class="person">
      <h2 class="person__name">Daniel Mercer</h2>
      <p class="person__role">Director &amp; Principal Solicitor</p>
      <p class="person__credentials">MBA, Juris Doctor</p>
    </section>

    <ul class="contacts">
      <li class="contacts__item">
        <svg class="contacts__icon" viewBox="0 0 24 24" fill="none" stroke="var(--gold)" stroke-width="2" stroke-linecap="round" stroke-linejoin="round"><path d="M5 3h4l2 5-3 2a11 11 0 0 0 6 6l2-3 5 2v4a2 2 0 0 1-2 2A17 17 0 0 1 3 5a2 2 0 0 1 2-2z"/></svg>
        +61 7 3000 4417
      </li>
      <li class="contacts__item">
        <svg class="contacts__icon" viewBox="0 0 24 24" fill="none" stroke="var(--gold)" stroke-width="2" stroke-linecap="round"><rect x="6" y="2" width="12" height="20" rx="2"/><line x1="11" y1="18" x2="13" y2="18"/></svg>
        +61 0400 312 968
      </li>
      <li class="contacts__item">
        <svg class="contacts__icon" viewBox="0 0 24 24" fill="none" stroke="var(--gold)" stroke-width="2" stroke-linejoin="round"><rect x="2" y="5" width="20" height="14" rx="1"/><path d="M2 6l10 7 10-7"/></svg>
        daniel@harlowlegal.com.au
      </li>
      <li class="contacts__item">
        <svg class="contacts__icon" viewBox="0 0 24 24" fill="none" stroke="var(--gold)" stroke-width="2"><circle cx="12" cy="12" r="10"/><ellipse cx="12" cy="12" rx="4" ry="10"/><line x1="2" y1="12" x2="22" y2="12"/></svg>
        www.harlowlegal.com.au
      </li>
    </ul>

    <address class="address">
      Level 3, Harlow House<br>
      88 Ridge Street,<br>
      Northgate, QLD 4000
    </address>
  </article>
</main>
</body>
</html>
```